Web Design for Webdesign company 3 page PSD

Project
---------
We need a PSD Web Design to be used in a WordPress installation.
What we would like to create is a professional looking website for a web design agency. We also need you to look for suitable stock images to be placed on these pages.
We need the design for:
Homepage
Landing page
Contact page
attached in the pages file you will find a file with more in depth details how these files should be build up.
We would like to see a desktop version and a mobile version of these pages
The website should have a 1100px width.
The mobile design should have 480px width.
The homepage should have a header slider about 450px high.
The slider is preferred full width and should have some images text and a button
Objectives
-------------
The main objective for the website is to get leads from customers in the form of a request for a quotation or a call or mail me back action. The most important action for the homepage is to link and navigate to our landing pages.
What we want to tell our visitors (our main products)
-------------------------------------------------------------------
- A website with no big investment but a monthly rate
- A successful website with no worries (a complete website, seo, hosting and a service contract for future customization is included for a monthly rate)
Color Scheme
------------
Use branding colors. You can find them in the branding.pdf file.
Additional colors:
White: #ffffff
Black: #181818
Company info
--------------
We are a starting web design / marketing agency based in The Netherlands and looking for the design of our website. Our services are (custom) webdesign, website marketing or combinations of both. Our main customer group is small business owners.
We sell websites but give the option to buy it with a lease contract.
A second product is a default website with a complete service: SEO, hosting and a service contract for a monthly rate.
Content:
-----------
If not available place Lorem Ipsum text.
There will come about 400 words of text on the landing pages
Design Competition
--------------------------
Since this is a designing competition we would like to see your creativity.
What you can expect from us is a lot of feedback 7 days a week with short response time.
You can send us the first sketchy mock ups of the homepage and we will give feedback based on these design. But we like your feedback or comments as well
Read the pages file for more in depth details how the pages should be designed

Target Market(s)
Small business owners in The Netherlands
Industry/Entity Type
It Company
Number of Pages Required
3 page
Requirements
Must have
- Homepage:
- Header slider with images, some text and a link to a custom page
- The slider should have 3 designed slides
- Landings page:
- Sidebar
- Action button for a request for a quotation
- Action button for a call me back action
- Action button for an appointment
- Contact form:
- Address details
- Contact form
Nice to have
- Homepage:
- Full width slider
- Testimonial block
- Blog items
Should not have
- Flash
- A to crowded design

```html
<!DOCTYPE html>
<html lang="en">
<head>
<meta charset="utf-8">
<title>Oak Ridge Web Studio</title>
<link href="https://fonts.googleapis.com/css2?family=Roboto:ital,wght@0,300;0,400;0,500;0,700;1,300;1,400&display=swap" rel="stylesheet">
<style>
:root{
  --ink:#181818;
  --dark:#1c1c1c;
  --white:#ffffff;
  --blue:#29a9d6;
  --mint:#66bb8f;
  --sage:#5b9479;
  --sage-btn:#5e9a7c;
  --text-gray:#6e6e6e;
  --foot-text:#b5b5b5;
}
*{margin:0;padding:0;box-sizing:border-box}
html,body{width:802px;height:1200px;overflow:hidden}
body{font-family:"Roboto",sans-serif;background:var(--white);color:var(--ink);position:relative}
.abs{position:absolute}

.site-header{left:0;top:0;width:802px;height:76px;background:var(--dark)}
.brand{left:50px;top:22px;display:flex;align-items:center;gap:8px;color:var(--white)}
.brand-mark{width:30px;height:30px;border-radius:50%;background:var(--white)}
.brand-name{font-weight:700;font-size:13px;line-height:1;letter-spacing:.2px}
.brand-tag{font-size:7px;font-weight:700;margin-top:3px}
.main-nav{left:335px;top:55px;display:flex;gap:20px;font-size:8.5px;font-weight:700;color:var(--white);letter-spacing:.3px}

.hero{left:0;top:76px;width:802px;height:278px;background:radial-gradient(ellipse at 70% 40%,#4a4a4a 0%,#2b2b2b 55%,#1e1e1e 100%)}
.hero-title{left:50px;top:130px;font-size:30px;font-weight:500;color:var(--mint);letter-spacing:.3px}
.hero-sub{left:50px;top:165px;font-size:24px;font-weight:500;color:var(--white);line-height:27px;letter-spacing:.3px}
.hero-btn{left:50px;top:234px;width:142px;height:35px;background:var(--blue);color:var(--white);font-size:12.5px;font-weight:500;display:flex;align-items:center;justify-content:center}
.hero-dots{left:50px;top:323px;display:flex;gap:5px}
.hero-dots span{width:7px;height:7px;border-radius:50%;background:var(--white)}
.hero-dots span.on{background:var(--blue)}
.hero-devices{left:304px;top:100px;width:492px;height:236px;background:linear-gradient(135deg,#6a6a6a,#9ccf5e 45%,#e8efe0 70%,#777);border-radius:6px;opacity:.9}

.promo{left:0;top:354px;width:802px;height:90px;background:linear-gradient(#ececec,#d9d9d9)}
.promo-devices{left:116px;top:1px;width:156px;height:86px;background:linear-gradient(135deg,#3a3a3a,#d8d8d8);border-radius:4px}
.promo-text{left:300px;top:33px;font-size:17px;font-weight:500;color:#2a2a2a;letter-spacing:.3px}
.promo-btn{left:633px;top:28px;width:120px;height:33px;background:var(--sage-btn);color:var(--white);font-size:12.5px;font-weight:500;display:flex;align-items:center;justify-content:center;letter-spacing:.5px}

.section-title{width:802px;left:0;text-align:center;font-size:19px;font-weight:500}
.para{font-size:8.6px;line-height:16px;font-weight:300;color:var(--text-gray);text-align:center;letter-spacing:.1px}
.btn-dark{background:var(--ink);color:var(--white);font-size:8.5px;font-weight:700;display:flex;align-items:center;justify-content:center;letter-spacing:.3px}

.welcome-title{top:469px;color:var(--blue)}
.welcome-text{left:52px;top:499px;width:698px}
.welcome-btn{left:350px;top:565px;width:102px;height:31px}

.services{left:0;top:618px;width:802px;height:210px;background:var(--sage)}
.services-title{top:22px;color:var(--white);font-size:18px}
.service-icon{width:81px;height:81px;border-radius:50%;background:var(--white);display:flex;align-items:center;justify-content:center}
.service-name{font-size:14.5px;font-weight:500;color:var(--white)}
.service-text{font-size:8.6px;line-height:16px;font-weight:300;color:#dbe9e1;width:242px;letter-spacing:.1px}
.service-btn{width:102px;height:31px}

.testi-title{top:851px;color:var(--blue);font-size:18px}
.quote-mark{font-size:30px;color:#b0b0b0;font-weight:700;line-height:1}
.testi-text{left:70px;top:881px;width:662px;font-style:italic}
.avatar{left:377px;top:944px;width:48px;height:48px;border-radius:50%;background:linear-gradient(#c9d8e6,#3d5f86)}
.testi-name{left:0;width:802px;top:1001px;text-align:center;font-size:9px;font-weight:500;color:var(--sage-btn)}
.testi-loc{left:0;width:802px;top:1014px;text-align:center;font-size:7.5px;color:#444}

.site-footer{left:0;top:1049px;width:802px;height:151px;background:var(--dark)}
.foot-head{font-size:14px;font-weight:500;color:var(--blue)}
.foot-divider{width:1px;height:99px;top:25px;background:#3a3a3a}
.blog-lead{left:50px;top:50px;font-size:8.8px;color:var(--mint)}
.blog-text{left:50px;top:64px;width:205px;font-size:8.6px;line-height:14px;color:var(--foot-text)}
.blog-more{left:50px;top:114px;font-size:7px;font-style:italic;color:var(--blue)}
.foot-links{display:grid;grid-template-columns:67px auto;row-gap:8px;font-size:8.5px;color:var(--foot-text)}
.social{left:526px;top:49px;display:flex;gap:3px}
.social span{width:20px;height:20px;border-radius:50%;background:#9a9a9a}
.foot-brand{left:526px;top:91px;font-size:6px;font-weight:700;color:var(--foot-text);width:38px;line-height:8px}
.copyright{left:574px;top:93px;font-size:7.5px;line-height:12px;color:var(--foot-text)}
</style>
</head>
<body>

<header class="site-header abs">
  <div class="brand abs">
    <span class="brand-mark"></span>
    <div>
      <div class="brand-name">OAK RIDGE<br>WEB STUDIO</div>
      <div class="brand-tag">Websites built to grow</div>
    </div>
  </div>
  <nav class="main-nav abs">
    <span>HOME</span><span>ABOUT US</span><span>SERVICES</span><span>PROJECTS</span><span>BLOG</span><span>TESTIMONIALS</span><span>CONTACT US</span>
  </nav>
</header>

<section class="hero abs">
  <div class="hero-devices abs" role="img" aria-label="Website shown responsive on desktop, laptop, tablet and phone screens"></div>
</section>
<h1 class="hero-title abs">Responsive Web Design</h1>
<p class="hero-sub abs">Your website readable<br>on all devices.</p>
<div class="hero-btn abs">More Information</div>
<div class="hero-dots abs"><span class="on"></span><span></span><span></span><span></span></div>

<section class="promo abs">
  <div class="promo-devices abs" role="img" aria-label="Online shop shown on a row of devices"></div>
  <p class="promo-text abs">Lorem ipsum dolor sit amet consect</p>
  <div class="promo-btn abs">WEB DESIGN</div>
</section>

<h2 class="section-title welcome-title abs">Welcome to Our Company Website</h2>
<p class="para welcome-text abs">Aliquam molestie, mi et imperdiet euismod, dui purus auctor tellus, et interdum lacus lectus et ante. Sed accumsan sollicitudin sapien, sit amet adipiscing turpis gravida ac. In congue, neque ac lobortis volutpat, libero mauris varius mi, vitae suscipit ipsum ligula vitae risus. Duis aliquam nibh a dui iaculis viverra id a velit. Vivamus egestas risus in magna varius commodo. Sed semper viverra egestas. Etiam pretium porttitor lectus, vel ornare neque porta volutpat...</p>
<div class="btn-dark welcome-btn abs">READ MORE</div>

<section class="services abs">
  <h2 class="section-title services-title abs">Our Company Services</h2>

  <div class="service-icon abs" style="left:50px;top:69px">
    <svg width="38" height="34" viewBox="0 0 38 34" fill="none" stroke="#6a6a6a" stroke-width="2.5">
      <rect x="2" y="4" width="34" height="21"/>
      <path d="M19 25v5M11 31h16"/>
      <path d="M12 20l3-6 14-12 3 3-12 14z" fill="#6a6a6a" stroke="none"/>
    </svg>
  </div>
  <h3 class="service-name abs" style="left:151px;top:66px">Web Design</h3>
  <p class="service-text abs" style="left:151px;top:88px">Aliquam molestie, mi et imperdiet euismod, dui purus auctor tellus, et interdum lacus lectus et ante. Sed accumsan sollicitudin sapien, sit amet adipiscing turpis gravida ac.</p>
  <div class="btn-dark service-btn abs" style="left:151px;top:150px">READ MORE</div>

  <div class="service-icon abs" style="left:411px;top:69px">
    <svg width="58" height="30" viewBox="0 0 58 30" fill="none" stroke="#6a6a6a" stroke-width="3">
      <path d="M14 5L3 15l11 10M44 5l11 10-11 10M33 2L25 28"/>
    </svg>
  </div>
  <h3 class="service-name abs" style="left:512px;top:66px">Development</h3>
  <p class="service-text abs" style="left:512px;top:88px">Aliquam molestie, mi et imperdiet euismod, dui purus auctor tellus, et interdum lacus lectus et ante. Sed accumsan sollicitudin sapien, sit amet adipiscing turpis gravida ac.</p>
  <div class="btn-dark service-btn abs" style="left:512px;top:150px">READ MORE</div>
</section>

<h2 class="section-title testi-title abs">Testimonials</h2>
<span class="quote-mark abs" style="left:48px;top:882px">&ldquo;</span>
<span class="quote-mark abs" style="left:735px;top:882px">&rdquo;</span>
<p class="para testi-text abs">Aliquam molestie, mi et imperdiet euismod, dui purus auctor tellus, et interdum lacus lectus et ante. Sed accumsan sollicitudin sapien, sit amet adipiscing turpis gravida ac. In congue, neque ac lobortis volutpat, libero mauris varius mi, vitae suscipit ipsum ligula vitae risus. Duis aliquam nibh a dui iaculis viverra id a velit. Vivamus egestas risus in magna varius commodo. Sed semper viverra egestas. Etiam pretium porttitor lectus, vel ornare neque porta volutpat...</p>
<div class="avatar abs" role="img" aria-label="Portrait photo of the client"></div>
<p class="testi-name abs">Name Heading</p>
<p class="testi-loc abs">Location</p>

<footer class="site-footer abs">
  <h4 class="foot-head abs" style="left:50px;top:22px">Blog Post</h4>
  <p class="blog-lead abs">Aliquam molestiemi et imperdiet euismod..</p>
  <p class="blog-text abs">Dui purus auctor tellus, et interdum lacus lectus et ante. Sed accumsan sollicitudin sapien, sit amet adipiscing turpis gravida ac.</p>
  <p class="blog-more abs">Continue Reading</p>

  <div class="foot-divider abs" style="left:289px"></div>

  <h4 class="foot-head abs" style="left:318px;top:22px">Company</h4>
  <div class="foot-links abs" style="left:318px;top:51px">
    <span>Home</span><span>Blog</span>
    <span>About Us</span><span>Testimonials</span>
    <span>Services</span><span>Contact Us</span>
    <span>Projects</span><span></span>
  </div>

  <div class="foot-divider abs" style="left:498px"></div>

  <h4 class="foot-head abs" style="left:526px;top:22px">Connect Us</h4>
  <div class="social abs" aria-label="Social media links"><span></span><span></span><span></span><span></span></div>
  <p class="foot-brand abs">OAK RIDGE WEB STUDIO</p>
  <p class="copyright abs">Copyright © 2015. Company Name.<br>All Right Reserved</p>
</footer>

</body>
</html>
```